Dog walking/Pet Sitting company needs a brochure to hook high end apartment tenants

We are looking for a brochure design that we can bring to meetings with high-end apartment and hotel management that will explain who we are, what we do, and how we can help their tenants/guests. I would like it to reflect the same look and feel of our website, carried over to printed brochure. Wesbite is www.hollowbrookpawcare.com. I can provide the stock images from the website if needed. A bi-fold brochure is ideal, unless you feel the information would fit better on a tri-fold. My company colors are #5D4664 and #5BA046. I would like a more professional tone to it, rather than fun.

Target Market(s)

Demo Professional Females and Males ages 30-50 with pets

Industry/Entity Type

Pet sitting

Font styles to use
Sans Serif

Colors
6b449b
9bcb3c

Requirements
Must have
• the same look and feel as my website; explain who we are, what we do, how we can help; include services offered; Mention that we service Parsippany and surrounding towns. Mention 15 years in business.
Should not have
• do not list pricing on brochure (you can mention pricing is available on the website). No cartoonish feel.

```html
<!DOCTYPE html>
<html lang="en">
<head>
<meta charset="utf-8">
<title>Hollowbrook Paw Care – Brochure</title>
<link href="https://fonts.googleapis.com/css2?family=Open+Sans:wght@400;600;700;800&display=swap" rel="stylesheet">
<style>
  :root{
    --plum:#5d4664;
    --plum-deep:#3b2b42;
    --plum-mid:#4a3752;
    --leaf:#5ba046;
    --ink:#3a3a3a;
    --paper:#ffffff;
    --paper-shade:#f3f2f4;
    --stage:#e6e7ea;
  }
  *{box-sizing:border-box;margin:0;padding:0}
  html,body{width:917px;height:1200px;overflow:hidden}
  body{background:var(--stage);font-family:"Open Sans",Arial,sans-serif;color:var(--ink);position:relative}
  .spread{position:absolute;left:25px;width:866px;height:560px;display:flex;box-shadow:0 6px 18px rgba(0,0,0,.18)}
  .spread--outer{top:22px}
  .spread--inner{top:614px}
  .page{position:relative;width:433px;height:560px;overflow:hidden}
  .photo{position:absolute;border-radius:2px}

  /* back cover */
  .back-cover{background:linear-gradient(200deg,var(--plum-deep) 0%,var(--plum-mid) 45%,var(--plum) 100%);color:#fff}
  .about__title{position:absolute;left:32px;top:34px;font-size:17px;font-weight:700;color:var(--leaf)}
  .about__body{position:absolute;left:32px;top:64px;width:370px;font-size:6.6px;line-height:1.5}
  .about__body p{margin-bottom:7px}
  .about__sign{position:absolute;left:32px;top:352px;font-size:6.8px;line-height:1.5}
  .about__sign strong{font-weight:700}
  .back-cover__rule{position:absolute;left:32px;right:32px;top:392px;height:1px;background:rgba(255,255,255,.35)}
  .photo--terrier{left:28px;top:410px;width:100px;height:130px;background:linear-gradient(180deg,#7b6a70,#c9a27c 55%,#f1ece6)}
  .contact{position:absolute;left:150px;top:452px;font-size:8px;line-height:1}
  .contact li{list-style:none;display:flex;align-items:center;gap:7px;margin-bottom:8px}
  .contact li:first-child{font-size:10px;font-weight:700}
  .contact svg{width:10px;height:10px;flex:none}
  .seal{position:absolute;left:318px;top:414px;width:84px;height:84px;border:1.5px solid rgba(255,255,255,.85);border-radius:50%;display:flex;align-items:center;justify-content:center;text-align:center;font-size:7.5px;font-weight:700;letter-spacing:.5px;line-height:1.3;color:#fff}

  /* front cover */
  .front-cover{background:var(--paper)}
  .brand{position:absolute;right:26px;top:24px;display:flex;align-items:center;gap:7px;font-size:11px;font-weight:700;color:var(--plum);letter-spacing:.4px;line-height:1.15;text-align:right}
  .brand__dot{width:14px;height:14px;border-radius:50%;background:var(--plum)}
  .photo--cover{left:0;top:78px;width:433px;height:482px;background:linear-gradient(160deg,#eef0f2 0%,#e3d8cc 40%,#b89a80 65%,#3a3234 80%,#8f9aa8 100%)}
  .cover-band{position:absolute;left:100px;right:0;top:372px;height:112px;background:linear-gradient(90deg,var(--plum-mid),var(--plum));color:#fff;padding:16px 22px 0 22px;text-align:right}
  .cover-band__lead{font-size:12.5px;font-weight:700;line-height:1.35}
  .cover-band__promise{font-size:12.5px;font-weight:700;color:var(--leaf);margin-top:4px}
  .cover-band__web{font-size:8px;font-weight:600;margin-top:6px}

  /* inner spread */
  .inside{background:var(--paper)}
  .inside--left{background:linear-gradient(90deg,var(--paper) 85%,var(--paper-shade))}
  .inside--right{background:linear-gradient(90deg,var(--paper-shade),var(--paper) 15%)}
  .ribbon{position:absolute;left:20px;top:22px;width:390px;height:26px;background:var(--plum);color:#fff;font-size:12px;font-weight:700;letter-spacing:.6px;display:flex;align-items:center;justify-content:center;clip-path:polygon(0 0,100% 0,96% 50%,100% 100%,0 100%)}
  .service{position:absolute}
  .service__title{font-size:9.5px;font-weight:700;color:var(--leaf);margin-bottom:3px}
  .service__intro{font-size:5.6px;line-height:1.45;margin-bottom:3px}
  .service__list{list-style:none;font-size:5.6px;line-height:1.5}
  .service__list li{position:relative;padding-left:8px}
  .service__list li::before{content:"";position:absolute;left:0;top:2.3px;width:4px;height:4px;border-radius:50%;background:var(--leaf)}
  .service__text{font-size:5.6px;line-height:1.5}
  .service--walking{left:24px;top:58px;width:380px}
  .service--sitting{left:24px;top:196px;width:210px}
  .service--sleepovers{left:24px;top:370px;width:180px}
  .photo--leash{left:262px;top:160px;width:150px;height:100px;background:linear-gradient(135deg,#d89a3a,#eed9b8 55%,#e9e4dc)}
  .photo--bowl{left:250px;top:290px;width:150px;height:100px;background:linear-gradient(135deg,#f0ece4,#dcbf8c 50%,#8a8680)}
  .photo--cuddle{left:210px;top:420px;width:160px;height:110px;background:linear-gradient(135deg,#f4f1ee,#c79a84 50%,#4b3b37)}
  .service--cat{left:30px;top:30px;width:230px}
  .service--boarding{left:30px;top:178px;width:235px}
  .service--wedding{left:30px;top:350px;width:200px}
  .photo--cat{left:272px;top:100px;width:140px;height:95px;background:linear-gradient(135deg,#c9ccd4,#e8dccc 45%,#b4a089)}
  .photo--blanket{left:272px;top:250px;width:140px;height:95px;background:linear-gradient(135deg,#9b6a5c,#5c4a54 45%,#8a8480)}
  .photo--wedding{left:240px;top:410px;width:170px;height:110px;background:linear-gradient(135deg,#c8c4b8,#e4e0d6 50%,#8f9aa0)}
</style>
</head>
<body>

<section class="spread spread--outer">
  <article class="page back-cover">
    <h2 class="about__title">About Us</h2>
    <div class="about__body">
      <p>We specialize in one-to-one personalized, quality pet care. We offer many services to cater to your needs. Whether you have dogs, cats, reptiles or rodents, we can help!</p>
      <p>Our business was born out of necessity. Years ago we were in the same boat as our clients, with a new puppy and long hours at work. We wanted a trusted, caring person to look after our pets when we could not, and we knew other owners felt exactly the same guilt, worry and fear.</p>
      <p>I imagined a company that could provide peace of mind for pet owners. A team that would treat every animal as family, keep strict schedules and report back after every visit. Today that vision is a reality, proudly serving Parsippany and surrounding towns for over 15 years.</p>
      <p>Today, we are a fully staffed company with employees, not contractors, who are insured, bonded and trained in pet first aid. We are proud of the trust our clients place in us and of the bond we build with every pet in our care.</p>
      <p>If you have pets and experience any feelings of guilt when you need to leave them behind, reach out to us! We pick right up where you leave off, with smiles, love and adventures that can turn an ordinary day extraordinary!</p>
    </div>
    <p class="about__sign"><strong>Dana Whitfield,</strong><br>Owner, Hollowbrook Paw Care LLC</p>
    <div class="back-cover__rule"></div>
    <div class="photo photo--terrier" role="img" aria-label="Photo of a small terrier holding a leather leash in its mouth"></div>
    <ul class="contact">
      <li><svg viewBox="0 0 10 10"><circle cx="5" cy="5" r="5" fill="#5ba046"/><path d="M3.2 2.6l1 1-.5.7c.4.8 1 1.4 1.8 1.8l.7-.5 1 1-.6.8C4.7 7.2 2.8 5.3 2.6 3.2z" fill="#fff"/></svg>201-555-0148</li>
      <li><svg viewBox="0 0 10 10"><circle cx="5" cy="5" r="5" fill="#5ba046"/><rect x="2.5" y="3.3" width="5" height="3.4" fill="none" stroke="#fff" stroke-width=".7"/><path d="M2.5 3.3L5 5.3l2.5-2" fill="none" stroke="#fff" stroke-width=".7"/></svg>hello@hollowbrookpawcare.com</li>
      <li><svg viewBox="0 0 10 10"><circle cx="5" cy="5" r="5" fill="#5ba046"/><circle cx="5" cy="5" r="2.6" fill="none" stroke="#fff" stroke-width=".7"/><path d="M2.4 5h5.2M5 2.4c-1.2 1.5-1.2 3.7 0 5.2M5 2.4c1.2 1.5 1.2 3.7 0 5.2" fill="none" stroke="#fff" stroke-width=".6"/></svg>www.hollowbrookpawcare.com</li>
    </ul>
    <div class="seal">HOLLOWBROOK<br>PAW CARE</div>
  </article>

  <article class="page front-cover">
    <div class="brand"><span class="brand__dot"></span><span>HOLLOWBROOK<br>PAW CARE</span></div>
    <div class="photo photo--cover" role="img" aria-label="Photo of a smiling woman hugging a black and white dog on a sofa"></div>
    <div class="cover-band">
      <p class="cover-band__lead">Prioritize Your Family, Career,<br>Health, Social Life, Goals, Yourself.</p>
      <p class="cover-band__promise">We'll Focus on Your Pets.</p>
      <p class="cover-band__web">www.hollowbrookpawcare.com</p>
    </div>
  </article>
</section>

<section class="spread spread--inner">
  <article class="page inside inside--left">
    <h1 class="ribbon">PROFESSIONAL PET CARE SERVICES</h1>

    <div class="service service--walking">
      <h3 class="service__title">Dog Walking</h3>
      <p class="service__intro">We are pleased to provide dog walking services Monday-Friday between the hours of 10:00 am and 5:00 pm.</p>
      <ul class="service__list">
        <li>Walking your dog (we offer a standard untimed visit and a guaranteed one-hour visit)</li>
        <li>Providing healthy exercise and fun</li>
        <li>Cleaning your dog after coming in from outside</li>
        <li>Feeding your dog and/or providing fresh water/treats</li>
        <li>Training reinforcement</li>
        <li>Grooming &amp; pampering your dog, such as brushing out coat</li>
        <li>Light pet related housekeeping (cleaning up accidents)</li>
        <li>Bringing in your mail/packages</li>
        <li>Providing you with an emailed/texted report along with photos</li>
      </ul>
    </div>
    <div class="photo photo--leash" role="img" aria-label="Photo of a yellow labrador holding a blue leash at a door"></div>

    <div class="service service--sitting">
      <h3 class="service__title">Pet Sitting</h3>
      <p class="service__intro">We are pleased to provide pet sitting services 7 days a week during the morning, afternoon and evening.</p>
      <ul class="service__list">
        <li>Three scheduled visits throughout the day</li>
        <li>Inclusive of all pets within the household</li>
        <li>Walking your dog and playing with your cat</li>
        <li>Providing healthy, fun exercise</li>
        <li>Cleaning your dog after coming in from outside</li>
        <li>Feeding your dog &amp; providing fresh water</li>
        <li>Emailed visit reports and pictures of your pets</li>
        <li>Pet sitting visits also include home care at no extra cost</li>
      </ul>
    </div>
    <div class="photo photo--bowl" role="img" aria-label="Photo of a labrador eating from a metal food bowl"></div>

    <div class="service service--sleepovers">
      <h3 class="service__title">Sleepovers</h3>
      <p class="service__text">Our newest option is becoming increasingly popular with pet parents who want their pets at home overnight. A sitter stays from evening to morning, so your pets keep their routine and never spend a night alone. Sleepovers can be combined with any daytime service for complete care.</p>
    </div>
    <div class="photo photo--cuddle" role="img" aria-label="Photo of a woman resting her head beside a sleeping dog"></div>
  </article>

  <article class="page inside inside--right">
    <div class="service service--cat">
      <h3 class="service__title">Cat Sitting / Small Pet Sitting</h3>
      <ul class="service__list">
        <li>One untimed visit per day (we stay until your cat is content)</li>
        <li>Socializing and playing with your cat</li>
        <li>Providing healthy mental stimulation and play</li>
        <li>Scooping litter box daily and full cleaning as needed</li>
        <li>Feeding your cat, providing fresh water/treats and cleaning the feeding area</li>
        <li>Emailed visit reports and pictures of your pet</li>
        <li>Cat sitting visits also include basic home care at no additional cost</li>
      </ul>
    </div>
    <div class="photo photo--cat" role="img" aria-label="Photo of a tabby cat being held in a person's arms"></div>

    <div class="service service--boarding">
      <h3 class="service__title">Day Care &amp; Overnight Boarding</h3>
      <p class="service__text">We understand that leaving your dog at home or in a kennel is not always the best option. That is why we offer in-home day care and boarding in a calm, safe setting. All guests must be current on vaccines and get along well with other dogs. While staying in our home, your dog will enjoy walks, play in a fenced yard and plenty of rest. We provide beds, bowls and toys; you provide their food and whatever else will make their stay more comfortable!</p>
    </div>
    <div class="photo photo--blanket" role="img" aria-label="Photo of two small dogs peeking out from under a striped blanket"></div>

    <div class="service service--wedding">
      <h3 class="service__title">Wedding Attendant</h3>
      <p class="service__text">When they are a part of your family, they should also be a part of your wedding! We make sure your dog gets to the venue, looks their best and is calm for photos and the ceremony. We handle transport, breaks, feeding and clean-up, then take your pet home when their part of the day is done. Each service can be customized to fit your needs so you can focus on the celebration. Check our blog for a look at a recent wedding we attended!</p>
    </div>
    <div class="photo photo--wedding" role="img" aria-label="Photo of a dog with a blue bow at an outdoor wedding"></div>
  </article>
</section>

</body>
</html>
```